Agrarhandel benötigt Homepage
Zielgruppe
Wir sind ein Agrarhandel mit einem Warenumschlagslager im Sinne eines klassischen Einzelhandels und vertreiben Produkte an Landwirte.
Wir vertreiben folgende Hauptproduktgruppen:
Einzelfuttermittel
wie z.B. Sojaexktraktionsschrot. Die einzelnen Produkte könnten z.B. wie die Futtermittel auf folgender Seite dargestellt werden (https://www.kornprobe-beispiel.eu/de/produkt/trelomixan)
Mischfuttermittel
Hier bieten wir unseren Kunden an, individuelles Mischfutter auf Basis unserer Einzelfuttermittel herzustellen.
Weitere Details und weitere Produktbereiche habe ich in einer Powerpoint-Übersicht dargestellt.
Neben diesen Produkten wollen wir uns als Familienunternehmen selbst vorstellen. Zudem betreiben wir in unserer Familie zusätzlich einen Milchviehbetrieb den wir ebenfalls hervorheben möchten, da wir unseren Kunden gegenüber einerseits als Zulieferer aber auch als Kollege auftreten wollen.
Einzelfuttermittel: Hier können wir durch unsere Unabhängigkeit punkten, da wir nicht abhängig von bestimmten Lieferanten sind und dementsprechend unabhängig beraten können. Wir untersuchen im Vergleich zu unseren Wettbewerben die Qualität der Futtermittel bis ins Detail und können daher eine Transparenz bieten, die Konkurrenten in der Regel nicht bieten können. Unser Warenumschlagsplatz mit moderner Technik ermöglicht es uns äußerst kosteneffizient die Waren umschlagen und ausliefern zu können.
Mischfuttermittel: Auf Basis der vorhandenen Einzelfuttermittel stellen wir je nach Kundenwunsch individuelle Mischfutter her. Wir arbeiten mit offenen Deklarationen, sodass unsere Kunden jederzeit nachvollziehen können, ob auch die Einzelfuttermittel verwendet wurden, die sie bestellt haben und keine billigen Ersatzprodukte verwendet wurden.
Zudem sind wir BT und HUPA zertifiziert. Die aktuellen für unser Unternehmen ausgestellten Zertifikate müssen für unsere Kunden als Download zur Verfügung stehen. Statt dem HUPA-Logo bitte das ..
Aufgabenstellung
Wir möchten gerne ein zeitgemäße Homepage, jedoch muss auch berücksichtigt werden, dass unsere Kunden eher konservativ denken.

```html
<!DOCTYPE html>
<html lang="de">
<head>
<meta charset="utf-8">
<title>Talgrund Agrarhandel – Einzelfuttermittel</title>
<link href="https://fonts.googleapis.com/css2?family=Lato:wght@400;700&display=swap" rel="stylesheet">
<style>
:root{
  --green:#3f6b52;
  --gold:#e4ae40;
  --ink:#1d1d1b;
  --muted:#6f7c74;
  --track:#ececec;
  --light:#f3f3f1;
  --card:#fbfbfb;
}
*{box-sizing:border-box;margin:0;padding:0}
html,body{width:1200px;height:2845px;overflow:hidden}
body{font-family:"Lato",sans-serif;color:var(--ink);background:#fff;position:relative}
.topbar{height:25px;background:var(--green);color:#fff;font-size:10px;display:flex;justify-content:flex-end;align-items:center;gap:18px;padding-right:99px}
.topbar span{display:flex;align-items:center;gap:5px}
.topbar .dot{width:12px;height:12px;border-radius:50%;background:var(--gold)}
.header{position:absolute;top:44px;left:100px;right:99px;height:62px;display:flex;align-items:center;justify-content:space-between}
.brand{display:flex;align-items:center;gap:12px;font-size:21px;font-weight:700;color:var(--green);letter-spacing:.3px}
.brand .mark{width:48px;height:48px;border-radius:50%;background:var(--gold)}
.nav{display:flex;gap:54px;font-size:15px;color:var(--muted)}
.nav .active{color:var(--gold)}
.intro{position:absolute;top:172px;left:100px;width:660px}
.intro .eyebrow{font-size:12px;font-weight:700}
.intro h1{font-size:37px;font-weight:700;margin:6px 0 20px}
.intro p{font-size:12.5px;line-height:19px}
.promo{position:absolute;left:874px;top:130px;width:194px;height:194px;border-radius:50%;background:var(--gold);padding:44px 0 0 30px}
.promo h2{font-size:27px;color:var(--green);font-weight:700;line-height:1}
.promo p{font-size:11px;font-weight:700;color:var(--green);line-height:16px;margin-top:4px}
.promo a{display:inline-block;margin-top:10px;background:var(--green);color:#fff;font-size:9px;padding:10px 25px;border-radius:6px;text-decoration:none}
.crumbs{position:absolute;left:100px;top:395px;font-size:12px}
.crumbs a{color:var(--ink)}
.crumbs .cur{color:var(--green);font-weight:700}
.sort{position:absolute;left:920px;top:386px;width:181px;height:34px;background:#efefef;font-size:13px;font-weight:700;display:flex;align-items:center;justify-content:space-between;padding:0 12px 0 6px}
.grid{position:absolute;left:100px;top:445px;display:grid;grid-template-columns:repeat(4,239px);column-gap:14px;row-gap:20px}
.card{height:412px;background:var(--card);border-radius:14px;box-shadow:0 2px 10px rgba(0,0,0,.06);padding:0 15px;position:relative}
.feed{width:118px;height:42px;margin:28px auto 0;border-radius:50% 50% 8px 8px/100% 100% 8px 8px}
.dark{background:linear-gradient(#8a4a22,#5a2a10)}
.yel{background:linear-gradient(#f2d675,#dcae3a)}
.gold{background:linear-gradient(#e8bd6e,#c98f3f)}
.card h3{font-size:13.5px;font-weight:700;margin:21px 0 14px}
.vals{list-style:none}
.vals li{font-size:8.5px;height:30px}
.vals b{display:block;height:6px;border-radius:3px;background:var(--track);margin-top:5px;position:relative}
.vals b::before{content:"";position:absolute;left:0;top:0;bottom:0;width:var(--w);min-width:4px;border-radius:3px;background:var(--green)}
.btn{position:absolute;left:64px;bottom:17px;width:111px;height:31px;border-radius:6px;background:var(--green);color:#fff;font-size:9.5px;display:flex;align-items:center;justify-content:center}
.signup{position:absolute;top:2211px;left:0;width:1200px;height:582px;background:var(--light)}
.signup h2{position:absolute;top:70px;width:100%;text-align:center;font-size:37px;font-weight:400}
.signup .lead{position:absolute;top:124px;left:305px;width:590px;text-align:center;font-size:12px;line-height:19px;color:#333}
.field{position:absolute;height:38px;border:1px solid #b7b7b7;border-radius:6px;background:#fff;font-size:12px;padding:0 30px;display:flex;align-items:center}
.consent{position:absolute;left:309px;top:413px;font-size:8.5px;line-height:14px;width:560px}
.send{position:absolute;left:309px;top:453px;width:102px;height:39px;border-radius:6px;background:var(--green);color:#fff;font-size:12px;display:flex;align-items:center;justify-content:center}
.footer{position:absolute;top:2793px;left:0;width:1200px;height:52px;background:var(--green);color:#fff;font-size:12px;display:flex;align-items:center;padding:0 100px}
.footer .legal{color:var(--gold);margin-left:57px}
.footer .legal+.legal{margin-left:74px}
.social{margin-left:auto;display:flex;gap:19px}
.social span{width:16px;height:16px;border-radius:3px;background:var(--gold)}
</style>
</head>
<body>
<div class="topbar">
  <span><i class="dot"></i>Feldstraße 4 - 84123 Musterau</span>
  <span><i class="dot"></i>info@talgrund-agrar.de</span>
  <span><i class="dot"></i>09100 12 34 56</span>
  <span><i class="dot"></i>0170 000 11 22</span>
</div>
<header class="header">
  <div class="brand"><span class="mark"></span>TALGRUND AGRARHANDEL</div>
  <nav class="nav"><span>Start</span><span class="active">Produkte</span><span>Über uns</span><span>Unser Qualitätsversprechen</span><span>Kontakt</span></nav>
</header>
<section class="intro">
  <div class="eyebrow">Produkte</div>
  <h1>Einzelfuttermittel</h1>
  <p>Entdecken Sie die Vielfalt unserer hochwertigen Einzelfuttermittel, bei denen sorgfältig ausgewählte Rohstoffe die Grundlage für ausgewogene Mischungen bilden. Mit bedacht eingesetzten Zusatzstoffen, Mineralstoffen, Vitaminen und wertvollen Spurenelementen gewährleisten wir optimale Versorgung. Erfahren Sie, wie diese Komponenten harmonisch zusammenwirken und ein qualitatives Futter für das Wohl Ihrer Tiere ergeben. Überzeugen Sie sich von den Vorteilen unserer Einzelfuttermittel!</p>
</section>
<aside class="promo">
  <h2>Jetzt Neu!</h2>
  <p>Kostenlos Registrieren für<br>tagesaktuelle Preisupdates!</p>
  <a>Jetzt Profitieren!</a>
</aside>
<div class="crumbs"><a>Start</a> &nbsp;/&nbsp; <a>Produkte</a> &nbsp;/&nbsp; <span class="cur">Einzelfuttermittel</span></div>
<div class="sort">Sortieren nach ...<svg width="12" height="8" viewBox="0 0 12 8"><path d="M1 1l5 5 5-5" fill="none" stroke="#333" stroke-width="1.5"/></svg></div>

<main class="grid">
<!-- row 1 -->
<article class="card"><div class="feed dark" role="img" aria-label="Futtermittelhaufen"></div><h3>HP-Sojaschrot</h3><ul class="vals"><li>Rohprotein: 46,9<b style="--w:43%"></b></li><li>nXP: 26,7<b style="--w:14%"></b></li><li>Rohfaser: 4,4<b style="--w:3%"></b></li><li>Rohfett: 2,7<b style="--w:1%"></b></li><li>UDP: 29,0<b style="--w:16%"></b></li><li>Zucker &amp; Stärke: 17,0<b style="--w:12%"></b></li><li>RNB: 32,3<b style="--w:25%"></b></li><li>NEL [MJ]: 7,8<b style="--w:5%"></b></li></ul><div class="btn">Produktdetails</div></article>
<article class="card"><div class="feed dark" role="img" aria-label="Futtermittelhaufen"></div><h3>HP-Sojaschrot GMO</h3><ul class="vals"><li>Rohprotein: 46,5<b style="--w:43%"></b></li><li>nXP: 26,0<b style="--w:14%"></b></li><li>Rohfaser: 3,5<b style="--w:3%"></b></li><li>Rohfett: 2,5<b style="--w:1%"></b></li><li>UDP: 28,0<b style="--w:16%"></b></li><li>Zucker &amp; Stärke: 15,8<b style="--w:11%"></b></li><li>RNB: 31,1<b style="--w:25%"></b></li><li>NEL [MJ]: 7,7<b style="--w:5%"></b></li></ul><div class="btn">Produktdetails</div></article>
<article class="card"><div class="feed yel" role="img" aria-label="Futtermittelhaufen"></div><h3>Rapsextraktionsschrot</h3><ul class="vals"><li>Rohprotein: 34,8<b style="--w:35%"></b></li><li>nXP: 22,6<b style="--w:14%"></b></li><li>Rohfaser: 12,7<b style="--w:3%"></b></li><li>Rohfett: 3,2<b style="--w:1%"></b></li><li>UDP: 35,0<b style="--w:46%"></b></li><li>Zucker &amp; Stärke: 7,0<b style="--w:7%"></b></li><li>RNB: 19,6<b style="--w:25%"></b></li><li>NEL [MJ]: 6,4<b style="--w:5%"></b></li></ul><div class="btn">Produktdetails</div></article>
<article class="card"><div class="feed gold" role="img" aria-label="Futtermittelhaufen"></div><h3>Provita Mais (Mehl / Pellets)</h3><ul class="vals"><li>Rohprotein: 28,5<b style="--w:31%"></b></li><li>nXP: 25,0<b style="--w:13%"></b></li><li>Rohfaser: 6,9<b style="--w:3%"></b></li><li>Rohfett: 11,3<b style="--w:1%"></b></li><li>UDP: 70,0<b style="--w:85%"></b></li><li>Zucker &amp; Stärke: 4,9<b style="--w:11%"></b></li><li>RNB: 5,6<b style="--w:3%"></b></li><li>NEL [MJ]: 7,4<b style="--w:5%"></b></li></ul><div class="btn">Produktdetails</div></article>
<!-- row 2 -->
<article class="card"><div class="feed dark" role="img" aria-label="Futtermittelhaufen"></div><h3>Trelomixan Rap</h3><ul class="vals"><li>Rohprotein: 46,9<b style="--w:43%"></b></li><li>nXP: 26,7<b style="--w:14%"></b></li><li>Rohfaser: 4,4<b style="--w:3%"></b></li><li>Rohfett: 2,7<b style="--w:1%"></b></li><li>UDP: 29,0<b style="--w:16%"></b></li><li>Zucker &amp; Stärke: 17,0<b style="--w:12%"></b></li><li>RNB: 32,3<b style="--w:25%"></b></li><li>NEL [MJ]: 7,8<b style="--w:5%"></b></li></ul><div class="btn">Produktdetails</div></article>
<article class="card"><div class="feed gold" role="img" aria-label="Futtermittelhaufen"></div><h3>Trelomixan Soy</h3><ul class="vals"><li>Rohprotein: 46,5<b style="--w:43%"></b></li><li>nXP: 26,0<b style="--w:14%"></b></li><li>Rohfaser: 3,5<b style="--w:3%"></b></li><li>Rohfett: 2,5<b style="--w:1%"></b></li><li>UDP: 28,0<b style="--w:16%"></b></li><li>Zucker &amp; Stärke: 15,8<b style="--w:11%"></b></li><li>RNB: 31,1<b style="--w:25%"></b></li><li>NEL [MJ]: 7,7<b style="--w:5%"></b></li></ul><div class="btn">Produktdetails</div></article>
<article class="card"><div class="feed dark" role="img" aria-label="Futtermittelhaufen"></div><h3>Veltra Raps</h3><ul class="vals"><li>Rohprotein: 34,8<b style="--w:35%"></b></li><li>nXP: 22,6<b style="--w:14%"></b></li><li>Rohfaser: 12,7<b style="--w:3%"></b></li><li>Rohfett: 3,2<b style="--w:1%"></b></li><li>UDP: 35,0<b style="--w:46%"></b></li><li>Zucker &amp; Stärke: 7,0<b style="--w:7%"></b></li><li>RNB: 19,6<b style="--w:25%"></b></li><li>NEL [MJ]: 6,4<b style="--w:5%"></b></li></ul><div class="btn">Produktdetails</div></article>
<article class="card"><div class="feed gold" role="img" aria-label="Futtermittelhaufen"></div><h3>Veltra Titan</h3><ul class="vals"><li>Rohprotein: 28,5<b style="--w:31%"></b></li><li>nXP: 25,0<b style="--w:13%"></b></li><li>Rohfaser: 6,9<b style="--w:3%"></b></li><li>Rohfett: 11,3<b style="--w:1%"></b></li><li>UDP: 70,0<b style="--w:85%"></b></li><li>Zucker &amp; Stärke: 4,9<b style="--w:11%"></b></li><li>RNB: 5,6<b style="--w:3%"></b></li><li>NEL [MJ]: 7,4<b style="--w:5%"></b></li></ul><div class="btn">Produktdetails</div></article>
<!-- row 3 -->
<article class="card"><div class="feed dark" role="img" aria-label="Futtermittelhaufen"></div><h3>Melasseschnitzelpellets</h3><ul class="vals"><li>Rohprotein: 46,9<b style="--w:43%"></b></li><li>nXP: 26,7<b style="--w:14%"></b></li><li>Rohfaser: 4,4<b style="--w:3%"></b></li><li>Rohfett: 2,7<b style="--w:1%"></b></li><li>UDP: 29,0<b style="--w:16%"></b></li><li>Zucker &amp; Stärke: 17,0<b style="--w:12%"></b></li><li>RNB: 32,3<b style="--w:25%"></b></li><li>NEL [MJ]: 7,8<b style="--w:5%"></b></li></ul><div class="btn">Produktdetails</div></article>
<article class="card"><div class="feed yel" role="img" aria-label="Futtermittelhaufen"></div><h3>Körnermais</h3><ul class="vals"><li>Rohprotein: 46,5<b style="--w:43%"></b></li><li>nXP: 26,0<b style="--w:14%"></b></li><li>Rohfaser: 3,5<b style="--w:3%"></b></li><li>Rohfett: 2,5<b style="--w:1%"></b></li><li>UDP: 28,0<b style="--w:16%"></b></li><li>Zucker &amp; Stärke: 15,8<b style="--w:11%"></b></li><li>RNB: 31,1<b style="--w:25%"></b></li><li>NEL [MJ]: 7,7<b style="--w:5%"></b></li></ul><div class="btn">Produktdetails</div></article>
<article class="card"><div class="feed dark" role="img" aria-label="Futtermittelhaufen"></div><h3>Zuckerrübenmelasse</h3><ul class="vals"><li>Rohprotein: 34,8<b style="--w:35%"></b></li><li>nXP: 22,6<b style="--w:14%"></b></li><li>Rohfaser: 12,7<b style="--w:3%"></b></li><li>Rohfett: 3,2<b style="--w:1%"></b></li><li>UDP: 35,0<b style="--w:46%"></b></li><li>Zucker &amp; Stärke: 7,0<b style="--w:7%"></b></li><li>RNB: 19,6<b style="--w:25%"></b></li><li>NEL [MJ]: 6,4<b style="--w:5%"></b></li></ul><div class="btn">Produktdetails</div></article>
<article class="card"><div class="feed dark" role="img" aria-label="Futtermittelhaufen"></div><h3>Rohglycerin</h3><ul class="vals"><li>Rohprotein: 28,5<b style="--w:31%"></b></li><li>nXP: 25,0<b style="--w:13%"></b></li><li>Rohfaser: 6,9<b style="--w:3%"></b></li><li>Rohfett: 11,3<b style="--w:1%"></b></li><li>UDP: 70,0<b style="--w:85%"></b></li><li>Zucker &amp; Stärke: 4,9<b style="--w:11%"></b></li><li>RNB: 5,6<b style="--w:3%"></b></li><li>NEL [MJ]: 7,4<b style="--w:5%"></b></li></ul><div class="btn">Produktdetails</div></article>
<!-- row 4 -->
<article class="card"><div class="feed gold" role="img" aria-label="Futtermittelhaufen"></div><h3>HP-Sojaschrot</h3><ul class="vals"><li>Rohprotein: 46,9<b style="--w:43%"></b></li><li>nXP: 26,7<b style="--w:14%"></b></li><li>Rohfaser: 4,4<b style="--w:3%"></b></li><li>Rohfett: 2,7<b style="--w:1%"></b></li><li>UDP: 29,0<b style="--w:16%"></b></li><li>Zucker &amp; Stärke: 17,0<b style="--w:12%"></b></li><li>RNB: 32,3<b style="--w:25%"></b></li><li>NEL [MJ]: 7,8<b style="--w:5%"></b></li></ul><div class="btn">Produktdetails</div></article>
<article class="card"><div class="feed gold" role="img" aria-label="Futtermittelhaufen"></div><h3>HP-Sojaschrot GMO</h3><ul class="vals"><li>Rohprotein: 46,5<b style="--w:43%"></b></li><li>nXP: 26,0<b style="--w:14%"></b></li><li>Rohfaser: 3,5<b style="--w:3%"></b></li><li>Rohfett: 2,5<b style="--w:1%"></b></li><li>UDP: 28,0<b style="--w:16%"></b></li><li>Zucker &amp; Stärke: 15,8<b style="--w:11%"></b></li><li>RNB: 31,1<b style="--w:25%"></b></li><li>NEL [MJ]: 7,7<b style="--w:5%"></b></li></ul><div class="btn">Produktdetails</div></article>
<article class="card"><div class="feed yel" role="img" aria-label="Futtermittelhaufen"></div><h3>Rapsextraktionsschrot</h3><ul class="vals"><li>Rohprotein: 34,8<b style="--w:35%"></b></li><li>nXP: 22,6<b style="--w:14%"></b></li><li>Rohfaser: 12,7<b style="--w:3%"></b></li><li>Rohfett: 3,2<b style="--w:1%"></b></li><li>UDP: 35,0<b style="--w:46%"></b></li><li>Zucker &amp; Stärke: 7,0<b style="--w:7%"></b></li><li>RNB: 19,6<b style="--w:25%"></b></li><li>NEL [MJ]: 6,4<b style="--w:5%"></b></li></ul><div class="btn">Produktdetails</div></article>
<article class="card"><div class="feed gold" role="img" aria-label="Futtermittelhaufen"></div><h3>Provita Mais (Mehl / Pellets)</h3><ul class="vals"><li>Rohprotein: 28,5<b style="--w:31%"></b></li><li>nXP: 25,0<b style="--w:13%"></b></li><li>Rohfaser: 6,9<b style="--w:3%"></b></li><li>Rohfett: 11,3<b style="--w:1%"></b></li><li>UDP: 70,0<b style="--w:85%"></b></li><li>Zucker &amp; Stärke: 4,9<b style="--w:11%"></b></li><li>RNB: 5,6<b style="--w:3%"></b></li><li>NEL [MJ]: 7,4<b style="--w:5%"></b></li></ul><div class="btn">Produktdetails</div></article>
</main>

<section class="signup">
  <h2>Erfahren Sie mehr, profitieren Sie mehr!</h2>
  <p class="lead">Verpassen Sie keine Marktchance! Melden Sie sich jetzt für unseren exklusiven Verteiler an und erhalten Sie täglich tagesaktuelle Preise für unsere Produkte. Mit uns sind Sie immer informiert und bereit, die besten Entscheidungen zu treffen.</p>
  <div class="field" style="left:309px;top:196px;width:582px">Name / Firma</div>
  <div class="field" style="left:309px;top:248px;width:410px">Adresse</div>
  <div class="field" style="left:732px;top:248px;width:159px">Haus-Nr.</div>
  <div class="field" style="left:309px;top:299px;width:133px">PLZ</div>
  <div class="field" style="left:456px;top:299px;width:435px">Ort</div>
  <div class="field" style="left:309px;top:352px;width:254px">Betriebsnummer</div>
  <div class="field" style="left:579px;top:352px;width:312px">E-Mail</div>
  <p class="consent">Durch die Anmeldung stimmst du der Verwendung deiner Daten für den Versand von tagesaktuellen Preisinhalten und Marketingmitteilungen zu und bestätigst unser <u>Datenschutzabkommen</u>.</p>
  <div class="send">Senden</div>
</section>

<footer class="footer">
  <span>© 2023 &nbsp;Talgrund Agrarhandel GbR</span>
  <span class="legal">Impressum</span>
  <span class="legal">Datenschutz</span>
  <div class="social"><span></span><span></span><span></span></div>
</footer>
</body>
</html>
```